Website for new crypto research organization

See brief (attached). This is a pretty basic website with only a handful of pages + ability to collect email addresses.

```html
<!DOCTYPE html>
<html lang="en">
<head>
<meta charset="utf-8">
<title>Seaglass Research</title>
<link href="https://fonts.googleapis.com/css2?family=Poppins:wght@400;500;600;700;800&family=Lato:wght@400;700&display=swap" rel="stylesheet">
<style>
:root{
  --teal:#1a9aa0;
  --teal-dark:#167f88;
  --navy:#0b2a4a;
  --deep:#061b33;
  --blue:#229fd6;
  --ink:#1d1d1d;
  --text:#444;
  --white:#fff;
  --black:#000;
  --line:#d9d9d9;
}
*{box-sizing:border-box;margin:0;padding:0}
html,body{width:1200px;height:2935px;overflow:hidden}
body{position:relative;background:var(--white);font-family:"Lato",sans-serif;color:var(--text)}
.abs{position:absolute}

/* hero */
.hero{left:0;top:0;width:1200px;height:644px;overflow:hidden}
.hero-bg{position:absolute;inset:0;background:
  radial-gradient(circle at 50% 40%,#1d6f8c 0%,#134a6e 35%,#0b2a4a 70%,#061b33 100%)}
.hero-edge{position:absolute;left:0;bottom:0;width:1200px;height:130px}
.logo-box{left:106px;top:39px;width:199px;height:121px;background:var(--white);display:flex;align-items:center;justify-content:center;z-index:2}
.logo-box span{font-family:"Poppins",sans-serif;font-weight:600;color:var(--teal);font-size:20px;line-height:1.15;text-align:center}
.nav{left:305px;top:65px;width:783px;height:68px;background:var(--white);border-radius:0 6px 6px 0;display:flex;align-items:center;padding-left:50px}
.nav a{font-family:"Lato",sans-serif;font-size:15px;color:#333;text-decoration:none;margin-right:55px;position:relative}
.nav a.active{color:var(--teal)}
.nav a.active::after{content:"";position:absolute;left:0;right:0;bottom:-6px;height:2px;background:var(--teal)}
.btn-login{position:absolute;right:12px;top:11px;width:103px;height:45px;background:var(--teal);color:#fff;font-family:"Poppins",sans-serif;font-weight:600;font-size:14px;display:flex;align-items:center;justify-content:center;border-radius:3px}
.hero-welcome{left:0;width:1200px;top:208px;text-align:center;color:#fff;font-family:"Poppins",sans-serif;font-size:33px;font-weight:400}
.hero-title{left:0;width:1200px;top:255px;text-align:center;color:#3bc0b2;font-family:"Poppins",sans-serif;font-weight:800;font-size:64px;line-height:72px;letter-spacing:2px}
.hero-copy{left:0;width:1200px;top:400px;text-align:center;color:#fff;font-size:15.5px;line-height:26px}
.btn-outline{left:536px;top:468px;width:128px;height:45px;border:2px solid #fff;border-radius:3px;color:#fff;font-family:"Poppins",sans-serif;font-weight:600;font-size:14px;display:flex;align-items:center;justify-content:center}
.arrow{top:300px;width:30px;height:44px}

/* about */
.about-art{left:112px;top:718px;width:489px;height:367px;border-radius:22px;background:#fff;box-shadow:0 2px 10px rgba(0,0,0,.2);padding:10px}
.about-art div{width:100%;height:100%;border-radius:14px;background:linear-gradient(120deg,#ff6fd8,#22e0c0 35%,#8b6bff 55%,#ff3b3b 75%,#38d1ff)}
.about-title{left:655px;top:708px;font-family:"Poppins",sans-serif;font-weight:600;font-size:29px;color:var(--ink)}
.rule{height:4px;border-radius:2px}
.about-rule{left:655px;top:759px;width:87px;background:var(--teal-dark)}
.about-copy{left:655px;top:795px;width:423px;font-size:15px;line-height:25.8px;text-align:justify;color:#444}
.btn-solid{background:var(--teal);color:#fff;font-family:"Poppins",sans-serif;font-weight:600;font-size:14px;display:flex;align-items:center;justify-content:center;border-radius:2px}
.about-btn{left:655px;top:1040px;width:140px;height:45px}

/* research */
.research{left:0;top:1171px;width:1200px;height:611px;background:
  radial-gradient(ellipse at 50% 30%,#136470 0%,#0b4356 40%,#072537 75%,#051a2b 100%)}
.research-title{left:0;width:1200px;top:1250px;text-align:center;color:#fff;font-family:"Poppins",sans-serif;font-weight:600;font-size:30px}
.research-rule{left:556px;top:1297px;width:88px;background:#fff;height:3px}
.card{top:1361px;width:316px;height:333px;border:2px solid #fff;padding:20px 30px;color:#fff}
.card.light{background:#fff;color:var(--ink)}
.card-head{display:flex;justify-content:space-between;align-items:center;height:60px}
.card-brand{font-family:"Poppins",sans-serif;font-weight:600;font-size:14px;line-height:1.1;color:#fff}
.card.light .card-brand{color:var(--teal)}
.card-date{font-family:"Poppins",sans-serif;font-size:15px;font-weight:500}
.card h3{font-family:"Poppins",sans-serif;font-weight:600;font-size:25px;margin:20px 0 16px}
.card p{font-size:15px;line-height:25.8px;text-align:justify}
.card .more{margin-top:14px;font-family:"Poppins",sans-serif;font-weight:600;font-size:15px}
.card.light .more{color:var(--teal)}

/* blog */
.blog-title{left:0;width:1200px;top:1856px;text-align:center;font-family:"Poppins",sans-serif;font-weight:500;font-size:31px;color:var(--ink)}
.post{top:1941px;width:311px;height:386px;border:2px solid #e4e4e4;padding:22px 20px;color:#333}
.post.featured{border-color:transparent;background:linear-gradient(180deg,#1a9f96,#229fd6);color:#fff}
.post h4{font-family:"Poppins",sans-serif;font-weight:500;font-size:20px;line-height:28px;color:var(--ink)}
.post.featured h4{color:#fff}
.post-meta{display:flex;justify-content:space-between;margin-top:38px;font-size:13.5px;text-transform:uppercase}
.post p{margin-top:30px;font-size:14px;line-height:25.8px}
.post .btn{margin-top:26px;width:123px;height:48px}
.post.featured .btn{background:#fff;color:var(--teal)}

/* footer */
.footer-edge{left:0;top:2428px;width:1200px;height:120px}
.footer{left:0;top:2540px;width:1200px;height:395px;background:var(--black);color:#fff}
.foot-h{top:2611px;font-family:"Poppins",sans-serif;font-weight:500;font-size:20px;color:#fff}
.foot-links{top:2667px;list-style:none;font-size:15px;line-height:25.8px;color:#fff}
.newsletter{left:111px;top:2672px;width:282px;height:48px;border-radius:24px;background:#eee;border:2px solid #fff}
.newsletter span{position:absolute;left:18px;top:13px;font-size:15px;color:#555}
.newsletter b{position:absolute;right:2px;top:2px;width:86px;height:40px;border-radius:20px;background:var(--blue);color:#fff;font-family:"Poppins",sans-serif;font-weight:600;font-size:14px;display:flex;align-items:center;justify-content:center}
.social{top:2671px;width:20px;height:20px;border-radius:50%;background:var(--blue)}
.copyright{left:0;width:1200px;top:2858px;text-align:center;font-size:15px;color:#fff}
</style>
</head>
<body>

<section class="hero abs">
  <div class="hero-bg" role="img" aria-label="Dark teal digital backdrop with glowing bokeh particles"></div>
  <svg class="hero-edge" viewBox="0 0 1200 130" preserveAspectRatio="none">
    <path fill="#fff" d="M0 70 L40 62 L70 80 L110 60 L150 75 L200 58 L240 82 L280 66 L300 90 L340 70 L380 98 L430 84 L470 104 L520 92 L560 112 L620 100 L660 118 L720 96 L760 108 L800 82 L850 96 L900 70 L940 84 L980 64 L1030 76 L1080 58 L1120 72 L1160 56 L1200 66 L1200 130 L0 130 Z"/>
  </svg>
</section>

<div class="logo-box abs"><span>SEAGLASS<br>RESEARCH</span></div>
<nav class="nav abs">
  <a class="active">Home</a><a>About</a><a>Research</a><a>News</a><a>Careers</a><a>Contact</a>
  <span class="btn-login">LOG IN</span>
</nav>

<svg class="arrow abs" style="left:66px" viewBox="0 0 30 44"><path d="M24 4 L8 22 L24 40" fill="none" stroke="#fff" stroke-width="5"/></svg>
<svg class="arrow abs" style="left:1104px" viewBox="0 0 30 44"><path d="M6 4 L22 22 L6 40" fill="none" stroke="#fff" stroke-width="5"/></svg>

<div class="hero-welcome abs">WELCOME TO</div>
<h1 class="hero-title abs">SEAGLASS<br>RESEARCH</h1>
<p class="hero-copy abs">Lorem ipsum dolor sit amet, consectetur adipiscing elit,<br>sed do eiusmod tempor incididunt ut labore</p>
<div class="btn-outline abs">GET STARTED</div>

<div class="about-art abs"><div role="img" aria-label="Colourful abstract artwork"></div></div>
<h2 class="about-title abs">ABOUT SEAGLASS RESEARCH</h2>
<div class="rule about-rule abs"></div>
<p class="about-copy abs">Lorem ipsum dolor sit amet, consectetur adipiscing elit, sed do eiusmod tempor incididunt ut labore et dolore magna aliqua. Ut enim ad minim veniam, quis nostrud exercitation ullamco laboris nisi ut aliquip ex ea commodo consequat. Duis aute irure dolor in reprehenderit in voluptate velit esse cillum dolore eu fugiat nulla pariatur. Excepteur sint occaecat cupidatat non proident, sunt in culpa qui officia deserunt mollit anim id est laborum.</p>
<div class="btn-solid about-btn abs">LEARN MORE</div>

<section class="research abs" role="img" aria-label="Dark teal digital grid backdrop with glowing particles"></section>
<h2 class="research-title abs">RESEARCH PROCESS</h2>
<div class="rule research-rule abs"></div>

<article class="card abs" style="left:109px">
  <div class="card-head"><span class="card-brand">SEAGLASS<br>RESEARCH</span><span class="card-date">09.02.2022</span></div>
  <h3>BEACON NETWORK</h3>
  <p>Lorem ipsum dolor sit amet, consectetur adipiscing elit, sed do eiusmod tempor incididunt ut labore et dolore magna aliqua.</p>
  <div class="more">Recent Research Reports →</div>
</article>
<article class="card light abs" style="left:441px">
  <div class="card-head"><span class="card-brand">SEAGLASS<br>RESEARCH</span><span class="card-date">09.02.2022</span></div>
  <h3>BEACON NETWORK</h3>
  <p>Lorem ipsum dolor sit amet, consectetur adipiscing elit, sed do eiusmod tempor incididunt ut labore et dolore magna aliqua.</p>
  <div class="more">Recent Research Reports →</div>
</article>
<article class="card abs" style="left:773px">
  <div class="card-head"><span class="card-brand">SEAGLASS<br>RESEARCH</span><span class="card-date">09.02.2022</span></div>
  <h3>BEACON NETWORK</h3>
  <p>Lorem ipsum dolor sit amet, consectetur adipiscing elit, sed do eiusmod tempor incididunt ut labore et dolore magna aliqua.</p>
  <div class="more">Recent Research Reports →</div>
</article>

<h2 class="blog-title abs">Latest Blog Posts</h2>

<article class="post abs" style="left:112px">
  <h4>Sed ut perspiciatis unde iste natus error sit</h4>
  <div class="post-meta"><span>By John Deo</span><span>February 09,2022</span></div>
  <p>Lorem ipsum dolor sit amet, consectetur adipiscing elit, sed do eiusmod tempor incididunt ut labore et dolore magna aliqua. Ut enim ad minim veniam, quis nostrud exercitation ullamco laboris nisi</p>
  <div class="btn btn-solid">READ MORE</div>
</article>
<article class="post featured abs" style="left:444px">
  <h4>Sed ut perspiciatis unde iste natus error sit</h4>
  <div class="post-meta"><span>By John Deo</span><span>February 09,2022</span></div>
  <p>Lorem ipsum dolor sit amet, consectetur adipiscing elit, sed do eiusmod tempor incididunt ut labore et dolore magna aliqua. Ut enim ad minim veniam, quis nostrud exercitation ullamco laboris nisi</p>
  <div class="btn btn-solid">READ MORE</div>
</article>
<article class="post abs" style="left:776px">
  <h4>Sed ut perspiciatis unde iste natus error sit</h4>
  <div class="post-meta"><span>By John Deo</span><span>February 09,2022</span></div>
  <p>Lorem ipsum dolor sit amet, consectetur adipiscing elit, sed do eiusmod tempor incididunt ut labore et dolore magna aliqua. Ut enim ad minim veniam, quis nostrud exercitation ullamco laboris nisi</p>
  <div class="btn btn-solid">READ MORE</div>
</article>

<svg class="footer-edge abs" viewBox="0 0 1200 120" preserveAspectRatio="none">
  <path fill="#000" d="M0 70 L30 60 L60 72 L90 40 L120 30 L150 50 L180 44 L210 66 L250 52 L290 70 L330 40 L370 34 L400 56 L440 42 L470 20 L510 38 L550 30 L590 50 L630 26 L680 40 L720 18 L760 30 L800 46 L840 28 L880 42 L930 30 L970 52 L1010 38 L1050 60 L1090 48 L1130 66 L1170 58 L1200 70 L1200 120 L0 120 Z"/>
</svg>
<footer class="footer abs"></footer>

<h3 class="foot-h abs" style="left:112px">NEWSLETTER SIGN UP</h3>
<div class="newsletter abs"><span>Your Email</span><b>SUBMIT</b></div>

<h3 class="foot-h abs" style="left:475px">QUICK LINKS</h3>
<ul class="foot-links abs" style="left:475px"><li>Home</li><li>About</li><li>Research</li><li>News</li><li>Careers</li><li>Contact</li></ul>

<h3 class="foot-h abs" style="left:686px">COMPANY</h3>
<ul class="foot-links abs" style="left:686px"><li>Terms&amp;condtions</li><li>Privacy Policy</li><li>About Us</li><li>Support</li></ul>

<h3 class="foot-h abs" style="left:875px">SOCIAL MEDIA</h3>
<span class="social abs" style="left:883px" aria-label="Social profile"></span>
<span class="social abs" style="left:926px" aria-label="Social profile"></span>

<p class="copyright abs">©Copyrights 2021 Company Name &nbsp;| &nbsp; All Rights Reserved</p>

</body>
</html>
```